Commercial Loan Originator Business Card (CHANGE COLORS SCHEME)

CHANGE COLOR SCHEME - SAME DESIGN

Name Marlene Agate
Title Commercial Loan Originator
Office (800) 417-2906 x68
Direct (240) 615-2043
Email freshgreens4life@quillbox.example

Name Dale Morrow
Office (800) 417-2906 x70
Direct (410) 392-5184
Email d.morthehomeguy@quillbox.example

Name Leonard Vasko
Office (800) 417-2906 x71
Direct (215) 463-0712
Email l.vasko41@quillbox.example

Name Gwen Halsey
Office (800) 417-2906 x
Direct (202) 548-1370
Email ghalsey63@quillbox.example

Name Mirna Ashby
Office (800) 417-2906 x72
Direct (240) 871-4526
Email tristatehomelending@quillbox.example

```html
<!DOCTYPE html>
<html lang="en">
<head>
<meta charset="UTF-8">
<title>Mirna Ashby – Commercial Loan Originator</title>
<link href="https://fonts.googleapis.com/css2?family=Montserrat:wght@500;700;800&display=swap" rel="stylesheet">
<style>
  :root {
    --page-bg: #d9d1c7;
    --card-bg: #ece6de;
    --card-edge: #f6f2ec;
    --ink: #1f1d1b;
    --ink-soft: #3a3633;
    --photo-light: #b9a48e;
    --photo-mid: #7d6653;
    --photo-dark: #3b2c24;
  }
  * { margin: 0; padding: 0; box-sizing: border-box; }
  html, body {
    width: 1200px;
    height: 1047px;
    overflow: hidden;
    background: var(--page-bg);
    font-family: "Montserrat", sans-serif;
    color: var(--ink);
  }
  .business-card {
    position: absolute;
    left: 100px;
    top: 251px;
    width: 1000px;
    height: 545px;
    background: var(--card-bg);
    border: 2px solid var(--card-edge);
    border-radius: 23px;
    overflow: hidden;
    box-shadow: 0 10px 30px rgba(60, 45, 35, 0.12);
  }
  .card-name {
    position: absolute;
    left: 48px;
    top: 127px;
    font-size: 39px;
    font-weight: 800;
    letter-spacing: 0.5px;
    text-transform: uppercase;
    line-height: 1;
  }
  .card-title {
    position: absolute;
    left: 48px;
    top: 184px;
    font-size: 21px;
    font-weight: 500;
    color: var(--ink-soft);
    line-height: 1;
  }
  .contact-list {
    position: absolute;
    left: 48px;
    top: 310px;
    list-style: none;
  }
  .contact-item {
    display: flex;
    align-items: center;
    height: 39px;
    font-size: 22px;
    font-weight: 500;
    color: var(--ink-soft);
  }
  .contact-icon {
    width: 20px;
    height: 20px;
    margin-right: 13px;
    fill: var(--ink);
    flex: none;
  }
  .portrait-area {
    position: absolute;
    left: 559px;
    top: 116px;
    width: 441px;
    height: 429px;
    background: linear-gradient(160deg, var(--photo-light) 0%, var(--photo-mid) 55%, var(--photo-dark) 100%);
    clip-path: polygon(14px 0, 100% 0, 100% 100%, 0 100%, 0 150px, 10px 140px);
  }
</style>
</head>
<body>
  <div class="business-card">
    <h1 class="card-name">Mirna Ashby</h1>
    <p class="card-title">Commercial Loan Originator</p>
    <ul class="contact-list">
      <li class="contact-item">
        <svg class="contact-icon" viewBox="0 0 24 24" aria-hidden="true"><path d="M2 9c0-3 4.5-5 10-5s10 2 10 5v2h-5V9c-1-.8-3-1.2-5-1.2S8 8.2 7 9v2H2zM6 12l2.5-3h7L18 12l2 8H4z"/></svg>
        (800) 417-2906 x72
      </li>
      <li class="contact-item">
        <svg class="contact-icon" viewBox="0 0 24 24" aria-hidden="true"><path d="M22 2 2 10.5l7 2.6L19 5l-8 9.6V22l3.8-5.2 4.7 3.2z"/></svg>
        (240) 871-4526
      </li>
      <li class="contact-item">
        <svg class="contact-icon" viewBox="0 0 24 24" aria-hidden="true"><path d="M2 5h20v14H2zm2 2v.4l8 5.3 8-5.3V7zm0 2.8V17h16V9.8l-8 5.3z"/></svg>
        tristatehomelending@quillbox.example
      </li>
    </ul>
    <div class="portrait-area" role="img" aria-label="Portrait photo of the loan originator seated in an office, smiling"></div>
  </div>
</body>
</html>
```